Birchwell Agency Condominium mail merge

We need a marketing proposal letter design to do a mail merge to potential e customers. We included our logo and an example of my miserable attempt to create a template. We are looking for a modern and attractive proposal template. Here is our website https://www.birchwellagency.example to be used for any additional information needed about us and our services.

Target Market(s)

New prospects

Industry/Entity Type

Insurance Agency

Requirements
Must have
• My project must have a modern professional look with merge fields similar to the file uploaded with this project.
Nice to have
• it would like have a condominium and a car icon graphic depicting there is additional discounts for both quotes bundled.
Should not have
• My project should not have any other logos or company name

```html
<!DOCTYPE html>
<html lang="en">
<head>
<meta charset="utf-8">
<title>Birchwell Agency – Letterhead</title>
<link rel="stylesheet" href="https://fonts.googleapis.com/css2?family=PT+Sans:wght@400;700&family=Arimo:wght@700&display=swap">
<style>
  :root {
    --brand-green: #3db54a;
    --brand-orange: #f47f20;
    --ink: #3b3b3b;
    --ink-strong: #111111;
    --paper: #ffffff;
    --rule: #555555;
  }
  * { margin: 0; padding: 0; box-sizing: border-box; }
  html, body {
    width: 1059px;
    height: 1200px;
    overflow: hidden;
    background: var(--paper);
  }
  .letter {
    position: relative;
    width: 1059px;
    height: 1200px;
    background: var(--paper);
    font-family: "PT Sans", "Myriad Pro", sans-serif;
    color: var(--ink);
  }
  .letter-header {
    position: absolute;
    top: 0; left: 0;
    width: 1059px;
    height: 160px;
  }
  .header-band {
    height: 26px;
    background: var(--brand-green);
  }
  .header-rule {
    height: 6px;
    background: var(--brand-orange);
  }
  .brand {
    position: absolute;
    top: 74px;
    left: 91px;
    display: flex;
    align-items: center;
    gap: 10px;
  }
  .brand-dot {
    width: 16px; height: 16px;
    border-radius: 50%;
    background: var(--brand-orange);
  }
  .brand-name {
    font-weight: 700;
    font-size: 34px;
    line-height: 40px;
    color: var(--brand-green);
  }
  .sender {
    position: absolute;
    top: 76px;
    right: 91px;
    text-align: right;
    line-height: 1.25;
  }
  .sender-name { font-weight: 700; font-size: 18px; color: var(--ink-strong); }
  .sender-role { font-size: 16px; color: var(--ink); }
  .letter-body {
    position: absolute;
    top: 268px;
    left: 91px;
    width: 877px;
  }
  .salutation {
    font-family: "Arimo", Arial, sans-serif;
    font-weight: 700;
    font-size: 19px;
    color: var(--ink-strong);
    margin-bottom: 22px;
  }
  .paragraph {
    font-size: 20.5px;
    line-height: 22.5px;
    letter-spacing: 0.15px;
    text-align: justify;
    margin-bottom: 21px;
  }
  .signature {
    margin-top: 36px;
    width: 170px;
    height: 66px;
    background: linear-gradient(90deg, #e9e9e9, #f5f5f5);
    border-radius: 4px;
  }
  .contact-box {
    position: absolute;
    left: 84px;
    top: 1121px;
    width: 906px;
    height: 50px;
    border: 1.5px dashed var(--rule);
    text-align: center;
    font-size: 14px;
    color: var(--ink);
    padding-top: 4px;
    line-height: 20px;
  }
  .contact-box .address { font-size: 13px; }
  .contact-sep { margin: 0 7px; }
  .footer-bar {
    position: absolute;
    left: 0; bottom: 0;
    width: 1059px;
    height: 12px;
    display: flex;
  }
  .footer-bar-green { flex: 1; background: var(--brand-green); }
  .footer-bar-orange { flex: 1; background: var(--brand-orange); }
</style>
</head>
<body>
<main class="letter">
  <header class="letter-header">
    <div class="header-band"></div>
    <div class="header-rule"></div>
    <div class="brand">
      <span class="brand-dot"></span>
      <span class="brand-name">Birchwell Agency</span>
    </div>
    <div class="sender">
      <div class="sender-name">Graham Birchwell</div>
      <div class="sender-role">Agency Principal</div>
    </div>
  </header>

  <section class="letter-body">
    <p class="salutation">Dear Mr. John,</p>
    <p class="paragraph">Lorem Ipsum is simply dummy text of the printing and typesetting industry. Lorem Ipsum has been the industry's standard dummy text ever since the 1500s, when an unknown printer took a galley of type and scrambled it to make a type specimen book. It has survived not only five centuries, but also the leap into electronic typesetting, remaining essentially unchanged.</p>
    <p class="paragraph">The standard chunk of Lorem Ipsum used since the 1500s is reproduced below for those interested. Sections 1.10.32 and 1.10.33 from "de Finibus Bonorum et Malorum" by Cicero are also reproduced in their exact original form, accompanied by English versions from the 1914 translation by H. Rackham</p>
    <p class="paragraph">Lorem Ipsum is simply dummy text of the printing and typesetting industry. Lorem Ipsum has been the industry's standard dummy text ever since the 1500s, when an unknown printer took a galley of type and scrambled it to make a type specimen book. It has survived not only five centuries, but also the leap into electronic typesetting, remaining essentially unchanged. It was popularised in the</p>
    <p class="paragraph">The standard chunk of Lorem Ipsum used since the 1500s is reproduced below for those interested. Sections 1.10.32 and 1.10.33 from "de Finibus Bonorum et Malorum" by Cicero are also reproduced in their exact original form, accompanied by English versions from the 1914 translation by H. Rackham</p>
    <p class="paragraph">The standard chunk of Lorem Ipsum used since the 1500s is reproduced below for those interested. Sections 1.10.32 and 1.10.33 from "de Finibus Bonorum et Malorum" by Cicero are also reproduced in their exact original form.</p>
    <div class="signature" role="img" aria-label="Handwritten signature of the agency principal"></div>
  </section>

  <footer>
    <div class="contact-box">
      <div class="address">2250 Harbor Lane Ste. 310 Lakemont, FL 32700</div>
      <div>555-014-2290<span class="contact-sep">|</span>graham@birchwellagency.example<span class="contact-sep">|</span>www.birchwellagency.example</div>
    </div>
    <div class="footer-bar">
      <span class="footer-bar-green"></span>
      <span class="footer-bar-orange"></span>
    </div>
  </footer>
</main>
</body>
</html>
```